VELMOR Website Design

We need a website designed for our company VELMOR. We are a luxury lifestyle club that will provide benefits and services for our members. The site should be clean & sleek, preferably using black and white (or darker colors). (example sites: stravenhall.example, plinth.example)

Here is a link of a sample page I did using wix. (https://dunmere7.sitehostly.example/mysite) This can be used to get a general idea.

Target Market(s)

Upper Middle Class in the United States

Number of Pages Required

5+ page

Font styles to use
Sans Serif
Other font styles liked:
• Arial (or other similar fonts)

Requirements
Must have
• A clean design that is eye-catching and speaks to our company.
Nice to have
• Ideas for copy.

```html
<!DOCTYPE html>
<html lang="en">
<head>
<meta charset="utf-8">
<title>VELMOR — A Members Only Lifestyle Club</title>
<link rel="stylesheet" href="https://fonts.googleapis.com/css2?family=Raleway:wght@300;400;500&family=Montserrat:wght@400;500;600&display=swap">
<style>
:root{
  --ink:#1c1c1c;
  --black:#0d0d0d;
  --white:#ffffff;
  --muted:#8a8a8a;
  --light:#f1f1f1;
  --brown:#6b4f36;
  --gold:#a8875a;
  --hero-a:#6d6a66;
  --hero-b:#3b3a38;
  --dark-a:#1f1f24;
  --dark-b:#2c2830;
}
*{margin:0;padding:0;box-sizing:border-box}
html,body{width:1200px;height:3056px;overflow:hidden}
body{font-family:"Montserrat",Arial,sans-serif;color:var(--ink);background:var(--white);position:relative}
section,header,footer{position:absolute;left:0;width:1200px;overflow:hidden}
.abs{position:absolute}
.heading{font-family:"Raleway",Arial,sans-serif;font-weight:400;letter-spacing:1px;text-transform:uppercase}
.center{text-align:center;left:0;width:1200px}
.rule{width:54px;height:2px;background:var(--gold);left:573px}
.btn{position:absolute;display:flex;align-items:center;justify-content:center;font-size:11px;letter-spacing:1px;text-transform:uppercase;color:var(--white)}
.btn--solid{background:var(--brown)}
.btn--outline{border:1px solid rgba(255,255,255,.8)}
.photo{position:absolute}

/* nav */
.site-nav{top:0;height:61px;z-index:3;background:rgba(0,0,0,.55)}
.brand{position:absolute;left:108px;top:14px;font-weight:400;font-size:25px;color:var(--white);letter-spacing:1px}
.menu{position:absolute;top:24px;left:455px;display:flex;font-size:10px;color:var(--white);letter-spacing:.5px}
.menu span{margin-right:54px}
.menu span:last-child{margin-right:0}

/* hero */
.hero{top:0;height:534px}
.hero-frame{left:306px;top:242px;width:587px;height:103px;border:1px solid rgba(255,255,255,.8);border-top:none}
.hero-frame-top{top:242px;height:1px;background:rgba(255,255,255,.8)}
.hero-title{top:224px;font-size:31px;color:var(--white)}
.hero-sub{top:282px;font-size:14px;color:var(--white)}
.scroll-cue{left:588px;top:488px;width:24px;height:32px;border:2px solid var(--white);border-radius:12px}
.scroll-cue::after{content:"";position:absolute;left:9px;top:7px;width:2px;height:10px;background:var(--white)}

/* welcome */
.welcome{top:534px;height:266px}
.sec-title{font-size:31px}
.para{font-size:11px;line-height:22px;color:#555}

/* services */
.services{top:800px;height:392px;background:linear-gradient(180deg,var(--dark-b),var(--dark-a))}
.card{position:absolute;top:168px;height:170px;overflow:hidden}
.card-label{position:absolute;left:0;right:0;bottom:0;height:36px;background:rgba(20,20,20,.75);color:var(--white);font-size:12px;letter-spacing:.5px;display:flex;align-items:center;justify-content:center;text-transform:uppercase}
.card--active{border:3px solid var(--white);top:162px;height:182px}
.card--active .card-label{background:var(--brown);left:10px;right:10px;bottom:8px}
.arrow-dot{position:absolute;width:26px;height:26px;border-radius:50%;background:var(--gold);top:237px}

/* video */
.video{top:1192px;height:438px}

/* split */
.split{top:1630px;height:336px}
.panel{position:absolute;top:0;height:336px;color:var(--white)}
.panel-title{font-family:"Raleway",Arial,sans-serif;font-weight:400;font-size:29px;text-transform:uppercase;letter-spacing:1px}
.panel-text{font-size:12px;line-height:28px}

/* events */
.events{top:1966px;height:393px}
.event-date{font-size:10px;color:#666}
.event-title{font-size:13px;font-weight:600;line-height:19px;color:var(--ink)}
.event-text{font-size:10px;line-height:17px;color:#999}

/* reviews */
.reviews{top:2359px;height:334px}
.review{position:absolute;top:118px;height:134px;background:var(--white)}
.review-text{position:absolute;left:96px;top:20px;width:210px;height:51px;overflow:hidden;font-size:10px;line-height:17px;color:#777}
.review-name{position:absolute;left:96px;top:96px;font-size:11px;font-weight:600;letter-spacing:.5px;text-transform:uppercase;color:var(--ink);white-space:nowrap}
.stars{color:var(--gold);font-size:10px;margin-left:14px;letter-spacing:1px}
.avatar{position:absolute;left:-20px;top:30px;width:86px;height:80px}
.nav-square{position:absolute;left:97px;width:60px;height:52px;background:var(--brown);transform:rotate(45deg) scale(.72)}

/* newsletter */
.newsletter{top:2693px;height:226px}
.field{position:absolute;left:350px;top:134px;width:460px;height:40px;background:var(--light);font-size:11px;font-style:italic;color:#999;padding:14px 18px}
.field-btn{position:absolute;left:810px;top:134px;width:40px;height:40px;background:var(--brown)}

/* footer */
.site-footer{top:2919px;height:137px;background:var(--black);color:var(--white)}
.foot-brand{position:absolute;left:208px;top:22px;font-size:27px;letter-spacing:2px}
.socials{position:absolute;left:222px;top:64px;display:flex;gap:10px}
.socials i{display:block;width:8px;height:8px;border-radius:50%;background:var(--white)}
.foot-menu{position:absolute;left:455px;top:24px;font-size:10px;display:flex}
.foot-menu span{margin-right:40px}
.contact{position:absolute;top:56px;display:flex;align-items:center;font-size:10px;white-space:nowrap}
.contact .ico{width:22px;height:22px;border:1px solid #555;margin-right:8px;display:flex;align-items:center;justify-content:center}
.foot-rule{position:absolute;left:0;top:104px;width:1200px;height:1px;background:#2e2e2e}
.legal{position:absolute;top:116px;font-size:9px;color:#cfcfcf;letter-spacing:.5px}
</style>
</head>
<body>

<section class="hero">
  <div class="photo" style="left:0;top:0;width:1200px;height:534px;background:linear-gradient(160deg,#7b7975 0%,#55524e 45%,#2f2e2c 100%)" role="img" aria-label="Four stylish people walking past a private jet on a sunny tarmac"></div>
  <div class="abs hero-frame"></div>
  <div class="abs hero-frame-top" style="left:306px;width:40px"></div>
  <div class="abs hero-frame-top" style="left:854px;width:39px"></div>
  <h1 class="abs center heading hero-title">A Members Only Lifestyle Club</h1>
  <p class="abs center hero-sub">VELMOR membership provides you with amazing benefits and services.</p>
  <a class="btn btn--outline" style="left:432px;top:326px;width:128px;height:36px">Join the Club</a>
  <a class="btn btn--solid" style="left:607px;top:326px;width:158px;height:36px">Member Login</a>
  <div class="abs scroll-cue"></div>
</section>

<header class="site-nav">
  <div class="brand">VELMOR</div>
  <nav class="menu"><span>HOME</span><span>ABOUT US</span><span>SERVICES &amp; BENEFITS</span><span>EVENTS</span><span>APPLY</span><span>CONTACT US</span></nav>
</header>

<section class="welcome">
  <h2 class="abs center heading sec-title" style="top:46px">Welcome to VELMOR</h2>
  <div class="abs rule" style="top:100px"></div>
  <p class="abs para" style="left:270px;top:116px;width:660px;text-align:center">VELMOR is a members only lifestyle club founded in order to bring the best services, experiences, and opportunities to our diverse community of members. Our members consist of creatives, athletes, artists, and other professionals.</p>
  <a class="btn btn--solid" style="left:544px;top:178px;width:122px;height:36px">Learn More</a>
</section>

<section class="services">
  <div class="photo" style="left:0;top:0;width:1200px;height:392px;background:linear-gradient(180deg,rgba(60,54,62,.6),rgba(20,20,26,.9))" role="img" aria-label="Crowd of cheering guests at a party, darkened"></div>
  <h2 class="abs center heading sec-title" style="top:46px;color:var(--white)">Services &amp; Benefits</h2>
  <div class="abs rule" style="top:100px"></div>
  <p class="abs center" style="top:118px;font-size:11px;color:#ddd">VELMOR membership provides you with amazing benefits and services.</p>

  <div class="card" style="left:122px;width:102px"><div class="photo" style="inset:0;background:linear-gradient(135deg,#4a4a50,#1d1d22)" role="img" aria-label="Business handshake"></div><div class="card-label" style="justify-content:flex-end;padding-right:6px">Services</div></div>
  <div class="card" style="left:240px;width:226px"><div class="photo" style="inset:0;background:linear-gradient(135deg,#2b3a5a,#0f1a30)" role="img" aria-label="Financial chart on a screen"></div><div class="card-label">Investment Services</div></div>
  <div class="card card--active" style="left:485px;width:230px"><div class="photo" style="inset:0;background:linear-gradient(160deg,#b23ab8,#4a1a6a 60%,#1a0f22)" role="img" aria-label="Concert crowd under purple stage lights"></div><div class="card-label">Investment Services</div></div>
  <div class="card" style="left:733px;width:226px"><div class="photo" style="inset:0;background:linear-gradient(180deg,#9fb6cc,#d8d2c6 60%,#8d8578)" role="img" aria-label="Travellers beside a private jet"></div><div class="card-label">Private Jet Travel</div></div>
  <div class="card" style="left:974px;width:104px"><div class="photo" style="inset:0;background:linear-gradient(135deg,#6a5a48,#2a241e)" role="img" aria-label="Lawyer signing documents"></div><div class="card-label" style="justify-content:flex-start;padding-left:50px">Lawyer</div></div>

  <div class="arrow-dot" style="left:96px"><svg width="26" height="26" viewBox="0 0 26 26"><path d="M15 8l-5 5 5 5" fill="none" stroke="#fff" stroke-width="2"/></svg></div>
  <div class="arrow-dot" style="left:1078px"><svg width="26" height="26" viewBox="0 0 26 26"><path d="M11 8l5 5-5 5" fill="none" stroke="#fff" stroke-width="2"/></svg></div>
  <div class="abs" style="left:597px;top:338px;width:7px;height:7px;border-radius:50%;background:var(--white)"></div>
</section>

<section class="video">
  <div class="photo" style="left:110px;top:54px;width:533px;height:332px;background:linear-gradient(180deg,#3b4658 0%,#6b7380 50%,#2b3140 100%)" role="img" aria-label="Private jet flying above the clouds"></div>
  <svg class="abs" style="left:352px;top:195px" width="50" height="50" viewBox="0 0 50 50"><circle cx="25" cy="25" r="23" fill="rgba(0,0,0,.55)" stroke="#fff" stroke-width="2"/><path d="M20 15l14 10-14 10z" fill="#fff"/></svg>
  <h2 class="abs heading sec-title" style="left:670px;width:420px;top:140px;text-align:center">Watch Our Video</h2>
  <p class="abs" style="left:670px;width:420px;top:196px;text-align:center;font-size:12px;line-height:26px">Learn more about our club by watching this quick video.<br>we're sure you will love it!</p>
  <a class="btn btn--solid" style="left:808px;top:258px;width:134px;height:34px">Apply Now</a>
</section>

<section class="split">
  <div class="panel" style="left:0;width:598px">
    <div class="photo" style="inset:0;background:linear-gradient(180deg,#3a3a3a,#1c1c1c)" role="img" aria-label="Crowd raising hands at an outdoor festival"></div>
    <h3 class="abs panel-title" style="left:108px;top:46px">Experiences</h3>
    <p class="abs panel-text" style="left:108px;top:108px;width:440px">VELMOR organizes and supports a ton of private events and parties for our members. Members are also provided access to exclusive venues and events from our partners. Network with other members to build lasting relationships.</p>
    <a class="btn btn--outline" style="left:108px;top:248px;width:120px;height:34px">Learn More</a>
  </div>
  <div class="panel" style="left:602px;width:598px">
    <div class="photo" style="inset:0;background:linear-gradient(180deg,#1e3a52,#2d4a4a 60%,#2a2520)" role="img" aria-label="Longtail boats on a tropical beach under limestone cliffs"></div>
    <h3 class="abs panel-title" style="right:110px;top:46px">We Are VELMOR</h3>
    <p class="abs panel-text" style="right:110px;top:108px;width:420px;text-align:right">Built in the image of a "Multi-Family Office", VELMOR provides members with access to just about any service, experience, and event desirable.<br>VELMOR is truly the most exclusive lifestyle club out there.</p>
    <a class="btn btn--outline" style="right:110px;top:248px;width:122px;height:34px">Apply Now</a>
  </div>
</section>

<section class="events">
  <h2 class="abs center heading sec-title" style="top:46px">Events</h2>
  <div class="abs rule" style="top:100px"></div>

  <div class="photo" style="left:110px;top:118px;width:240px;height:162px;background:linear-gradient(135deg,#3aa0c8,#c8b040 50%,#b03a6a)" role="img" aria-label="DJ performing on a colourful festival stage"></div>
  <p class="abs event-date" style="left:370px;top:126px">4th october 2018</p>
  <p class="abs event-title" style="left:370px;top:146px;width:220px">Lorem ipsum dolor sit consectetur adipiscing elit.</p>
  <p class="abs event-text" style="left:370px;top:190px;width:210px">Suspendisse at nunc ut libero gravida fringilla. Vestibulum pretium luctus tincidunt. Fusce justo magna, ornare eu mauris eleifend congue felis... [+]</p>
  <div class="abs" style="left:600px;top:122px;width:1px;height:150px;background:#ddd"></div>

  <div class="photo" style="left:625px;top:118px;width:240px;height:162px;background:radial-gradient(circle at 50% 50%,#e08a30,#6a2a10 45%,#120806 80%)" role="img" aria-label="Fire spinning performer creating a spiral of sparks at night"></div>
  <p class="abs event-date" style="left:885px;top:126px">10th october 2018</p>
  <p class="abs event-title" style="left:885px;top:146px;width:220px">Lorem ipsum dolor sit consectetur adipiscing elit.</p>
  <p class="abs event-text" style="left:885px;top:190px;width:210px">Suspendisse at nunc ut libero gravida fringilla. Vestibulum pretium luctus tincidunt. Fusce justo magna, ornare eu mauris eleifend congue felis... [+]</p>

  <a class="btn btn--solid" style="left:518px;top:306px;width:160px;height:34px">View All Events</a>
</section>

<section class="reviews">
  <div class="photo" style="left:0;top:0;width:1200px;height:334px;background:linear-gradient(180deg,#3a3c48,#0c0c10)" role="img" aria-label="Luxury villa with pool at dusk, darkened"></div>
  <h2 class="abs center heading sec-title" style="top:44px;color:var(--white)">Members Reviews</h2>
  <div class="abs rule" style="top:98px"></div>

  <div class="nav-square" style="top:128px;background:transparent;border:2px solid #fff"></div>
  <svg class="abs" style="left:114px;top:144px" width="26" height="20" viewBox="0 0 26 20"><path d="M3 10h19M15 3l7 7-7 7" fill="none" stroke="#fff" stroke-width="2.5"/></svg>
  <div class="nav-square" style="top:180px"></div>
  <svg class="abs" style="left:114px;top:196px" width="26" height="20" viewBox="0 0 26 20"><path d="M23 10H4M11 3l-7 7 7 7" fill="none" stroke="#fff" stroke-width="2.5"/></svg>

  <article class="review" style="left:262px;width:323px">
    <div class="avatar" style="background:linear-gradient(180deg,#c9c2b8,#5a5550)" role="img" aria-label="Portrait of a member"></div>
    <p class="review-text">Suspendisse at nunc ut libero gravida fringilla. Vestibulum pretium luctus tincidunt. Fusce justo magna, ornare eu mauris eleifend congue felis.</p>
    <p class="review-name">Marek Ellison<span class="stars">★★★★★</span></p>
  </article>
  <article class="review" style="left:630px;width:320px">
    <div class="avatar" style="background:linear-gradient(180deg,#e0d4c4,#a89070)" role="img" aria-label="Portrait of a member"></div>
    <p class="review-text">Suspendisse at nunc ut libero gravida fringilla. Vestibulum pretium luctus tincidunt. Fusce justo magna, ornare eu mauris eleifend congue felis.</p>
    <p class="review-name">Lena Vasquel<span class="stars">★★★★★</span></p>
  </article>
  <article class="review" style="left:1040px;width:320px">
    <div class="avatar" style="background:linear-gradient(180deg,#d0c8c0,#6a6058)" role="img" aria-label="Portrait of a member"></div>
    <p class="review-text">Suspendisse at nunc ut libero gravida fringilla. Vestibulum pretium luctus tincidunt. Fusce justo magna, ornare eu mauris eleifend congue felis.</p>
    <p class="review-name">Owen Hartley<span class="stars">★★★★★</span></p>
  </article>
</section>

<section class="newsletter">
  <h2 class="abs center heading sec-title" style="top:46px">Subscribe to Our Newsletter</h2>
  <p class="abs center" style="top:98px;font-size:11px;color:var(--muted)">Subscribe to our newsletter to receive all the latest VELMOR news and updates to your inbox</p>
  <div class="field">Enter Your Email Address...</div>
  <div class="field-btn"><svg width="40" height="40" viewBox="0 0 40 40"><path d="M13 20l15-7-5 15-3-6z" fill="#fff"/></svg></div>
</section>

<footer class="site-footer">
  <div class="foot-brand">VELMOR</div>
  <div class="socials"><i></i><i></i><i></i><i></i><i></i></div>
  <nav class="foot-menu"><span>HOME</span><span>ABOUT US</span><span>SERVICES &amp; BENEFITS</span><span>EVENTS</span><span>APPLY</span><span>CONTACT US</span></nav>
  <div class="contact" style="left:455px">
    <span class="ico"><svg width="10" height="12" viewBox="0 0 10 12"><path d="M5 0a4 4 0 0 0-4 4c0 3 4 8 4 8s4-5 4-8a4 4 0 0 0-4-4zm0 5.5A1.5 1.5 0 1 1 5 2.5a1.5 1.5 0 0 1 0 3z" fill="#fff"/></svg></span>VELMOR 48 Alder Row, Fairhaven 20410
  </div>
  <div class="contact" style="left:752px">
    <span class="ico"><svg width="11" height="11" viewBox="0 0 11 11"><path d="M2 0l2 2.5-1 1.5c.7 1.5 2 2.8 3.5 3.5l1.5-1L11 9l-2 2C4.5 10.5.5 6.5 0 2z" fill="#fff"/></svg></span>555-014-2290
  </div>
  <div class="contact" style="left:882px">
    <span class="ico"><svg width="12" height="9" viewBox="0 0 12 9"><rect x=".5" y=".5" width="11" height="8" fill="none" stroke="#fff"/><path d="M.5.5L6 5l5.5-4.5" fill="none" stroke="#fff"/></svg></span>info@velmor.example
  </div>
  <div class="foot-rule"></div>
  <p class="legal" style="left:208px">© COPYRIGHT 2018 VELMOR. ALL RIGHTS RESERVED.</p>
  <p class="legal" style="left:872px">PRIVACY | POLICY | FAQS</p>
</footer>

</body>
</html>
```